Redesign of business card for Cedar Ridge Mechanical

We are looking for a new design for our business cards for Cedar Ridge Mechanical. We are a plumbing & HVAC construction company, operating on the West Coast of Canada and USA. Logo attached.
Industry/Entity Type
Construction - Plumbing & HVAC
Contact Information for Business Card
Name, address, phone numbers, email, website address
Look and feel
Each slider illustrates characteristics of the customer's brand and the style your logo design should communicate.

```html
<!DOCTYPE html>
<html lang="en">
<head>
<meta charset="utf-8">
<title>Cedar Ridge Mechanical – Business Card</title>
<link href="https://fonts.googleapis.com/css2?family=Montserrat:wght@400;500;700&display=swap" rel="stylesheet">
<style>
  :root {
    --stage: #1c1c1c;
    --card-dark: #151515;
    --card-light: #ffffff;
    --swoosh: #9a9a9a;
    --ink-dark: #141414;
    --ink-muted: #8a8a8a;
    --ink-light: #ffffff;
  }
  * { margin: 0; padding: 0; box-sizing: border-box; }
  html, body {
    width: 1200px; height: 963px; overflow: hidden;
    background: var(--stage);
    font-family: "Montserrat", sans-serif;
  }
  .stage {
    width: 1200px; height: 963px;
    display: flex; flex-direction: column; align-items: center; justify-content: center;
    gap: 43px;
  }
  .card {
    position: relative;
    width: 700px; height: 400px;
    border-radius: 22px;
    overflow: hidden;
    box-shadow: 0 12px 30px rgba(0,0,0,.55);
  }
  .card-front { background: var(--card-light); }
  .card-front .sweep { position: absolute; inset: 0; }
  .person { position: absolute; left: 38px; top: 34px; color: var(--ink-dark); }
  .person-name { font-weight: 700; font-size: 24px; letter-spacing: .5px; text-transform: uppercase; }
  .person-name .surname { color: var(--ink-muted); }
  .person-role { font-size: 15px; color: var(--ink-muted); margin-top: 2px; }
  .contact { position: absolute; left: 38px; top: 250px; list-style: none; color: var(--ink-light); }
  .contact li { display: flex; align-items: center; gap: 10px; font-size: 17px; line-height: 28px; }
  .contact svg { width: 15px; height: 15px; flex: none; }
  .brand { position: absolute; display: flex; align-items: center; gap: 10px; color: var(--ink-light); white-space: nowrap; }
  .brand-mark { width: 16px; height: 16px; background: var(--ink-light); }
  .brand-name { font-weight: 700; font-size: 20px; letter-spacing: 1px; text-transform: uppercase; }
  .card-front .brand { right: 38px; top: 276px; }
  .address { position: absolute; right: 38px; top: 318px; text-align: right; color: var(--ink-light); font-size: 17px; line-height: 24px; }
  .card-back { background: var(--card-dark); display: flex; align-items: center; justify-content: center; }
  .card-back .back-frame {
    position: absolute; inset: 26px; border-radius: 16px;
    background: #1d1d1d;
  }
  .card-back .brand { position: relative; }
  .card-back .brand-name { font-size: 34px; }
  .card-back .brand-mark { width: 26px; height: 26px; }
</style>
</head>
<body>
<main class="stage">
  <section class="card card-front">
    <svg class="sweep" viewBox="0 0 700 400" preserveAspectRatio="none" aria-hidden="true">
      <path d="M300,148 C470,140 620,175 700,232 L700,262 C580,185 450,150 300,148 Z" fill="var(--swoosh)"/>
      <path d="M0,196 C180,150 470,128 700,262 L700,400 L0,400 Z" fill="var(--card-dark)"/>
    </svg>
    <div class="person">
      <div class="person-name">Marcus <span class="surname">Reid</span></div>
      <div class="person-role">Manager</div>
    </div>
    <ul class="contact">
      <li><svg viewBox="0 0 16 16"><path d="M3 1h3l1 4-2 1a9 9 0 0 0 5 5l1-2 4 1v3a2 2 0 0 1-2 2A13 13 0 0 1 1 3a2 2 0 0 1 2-2z" fill="#fff"/></svg>123-456-2100</li>
      <li><svg viewBox="0 0 16 16"><rect x="1" y="3" width="14" height="10" rx="1" fill="#fff"/><path d="M1.5 3.5 8 9l6.5-5.5" stroke="#151515" stroke-width="1.4" fill="none"/></svg>youremail@mailbox.com</li>
      <li><svg viewBox="0 0 16 16"><circle cx="8" cy="8" r="7" fill="#fff"/><path d="M1 8h14M8 1c-3 3-3 11 0 14M8 1c3 3 3 11 0 14" stroke="#151515" stroke-width="1.1" fill="none"/></svg>www.yourwebsite.com</li>
    </ul>
    <div class="brand"><span class="brand-mark"></span><span class="brand-name">Cedar Ridge Mechanical</span></div>
    <p class="address">Your address, city<br>state, ZIP 0000</p>
  </section>

  <section class="card card-back">
    <div class="back-frame"></div>
    <div class="brand"><span class="brand-mark"></span><span class="brand-name">Cedar Ridge Mechanical</span></div>
  </section>
</main>
</body>
</html>
```